Doctor Formulated Medical Cosmetics

Velour Skinhaus is an E-commerce site for high end Medical Cosmetics designed to treat specific skin problems. The Velour Skinhaus difference/advantage is that all creams and serums are:
Doctor Formulated, Freshly Handmade, Registered Pharmacy.
The Site also provides real doctor Dermatology Consultations, Library (with a list of - 1. Active Ingredients in the creams with description of their effects, 2. Skin Conditions with information on what causes the condition and typical treatment approaches and outcomes. 3. Resources from Dermatology Journals and literature on the conditions.)
Header Information: Velour Skinhaus, languages EN, BG, Register / log in, Shopping Bag. This field should be narrow.
Categories (horizontal): Home, Face, Body, Hair Care, Skin Conditions, Doctor Consultation, Library
The Landing Page should have only one well organized picture, which is intended to create the feeling of luxury, freedom and relaxation. It will be large and will fill the whole screen. All text should be on transparent or similar color fields. Please use the color of the text to create also the feeling of conservative luxury.
Written message / image overlay Velour Skinhaus(logo), Skin Care, Doctor Formulated, Freshly Handmade, Registered Pharmacy.
Please study the Landing Page of this site as an example: www.marivane.com
Under the Landing Page, there should be a slider with 4 of our products.
Underneath: Four Blog Articles (large pictures for maximum impact and luxury text underneath).
Underneath: Banner for Dermatologist Consultation, (button for Start Your Case Now).
Underneath: Two pictures in a line - Library (with books), and Active Ingredients.
Footer: Philosophy, Categories, Customer Care
Please adhere to the color palate provided in the pictures (as attachments). Provided are some examples of Web Sites with the desired look and feel. www.quillora.com , www.tavenholtmd.com .
Please use different shades of gray, white, beige and gold colors, and black. Our products will be in brown glass jars and bottles to convey the professional, pharmacy made nature of the creams and lotions.
We find the following Front Page very attractive and effective - www.marivane.com , with its full page image and overlaying text.
Please have a look at this link for the Landing page.
http://www.brimlensphoto.com/detail/video/woman-lying-on-a-black-sand-beach-in-a-bikini-stock-footage/58213067
I would like to use it in the animated version to achieve the WOW effect. I have uploaded the jpeg version for it, so you will be able create your design.
For the Landing page design, please use only the two uploaded pictures of a woman laying at the beach. Let's see how each of them will look like.
Thank you for your help.

```html
<!DOCTYPE html>
<html lang="en">
<head>
<meta charset="utf-8">
<title>Velour Skinhaus — Doctor Formulated Medical Cosmetics</title>
<link rel="stylesheet" href="https://fonts.googleapis.com/css2?family=Lato:ital,wght@0,400;0,700;1,400&family=Lora:ital@0;1&family=Playfair+Display:wght@400&display=swap">
<style>
:root{
  --ink:#1f1c19;
  --ink-soft:#3a3532;
  --gold:#c9a55a;
  --gold-dark:#a9843c;
  --gold-light:#e3c98d;
  --cream:#eef0e4;
  --mist:#f4f5f7;
  --paper:#ffffff;
  --line:#e3e3e3;
  --text:#333333;
  --muted:#777777;
  --foot:#f2f2f2;
}
*{box-sizing:border-box;margin:0;padding:0}
html,body{width:1200px;height:3243px;overflow:hidden}
body{position:relative;background:var(--paper);font-family:"Lato",Arial,sans-serif;color:var(--text)}
section,header,nav,footer{position:absolute;left:0;width:1200px}
h2,h3,h4{font-weight:400}

/* header */
.topbar{top:0;height:93px;background:var(--ink)}
.brand{position:absolute;left:86px;top:26px;display:flex;align-items:center;gap:12px;color:var(--gold);font-size:32px;letter-spacing:.5px}
.brand-ring{display:block;width:40px;height:40px;border:2px solid var(--gold);border-radius:50%}
.util{position:absolute;right:230px;top:37px;display:flex;gap:22px;font-size:13px;color:var(--gold-light)}
.util span::before{content:"▪";margin-right:6px;font-size:9px;color:var(--gold)}
.lang{position:absolute;right:150px;top:30px;display:flex}
.lang b{display:block;width:30px;height:30px;line-height:30px;text-align:center;font-size:12px;font-weight:400;color:#fff;border:1px solid #555}
.lang b.on{background:var(--gold);border-color:var(--gold)}
.bag{position:absolute;right:86px;top:24px;width:44px;height:44px;border:2px solid var(--gold);border-radius:50%;display:flex;align-items:center;justify-content:center}
.mainnav{top:93px;height:54px;background:linear-gradient(#d8b873,var(--gold) 60%,#b99248);display:flex;justify-content:center;align-items:center;gap:48px;font-size:14px;color:#fff}

/* hero */
.hero{top:147px;height:489px;background:var(--cream);overflow:hidden}
.hero-photo{position:absolute;left:0;top:0;width:1200px;height:489px;
  background:
    radial-gradient(ellipse 38% 75% at 24% 55%,rgba(176,128,80,.95) 0%,rgba(196,152,104,.85) 40%,rgba(220,200,160,0) 100%),
    radial-gradient(ellipse 22% 40% at 30% 30%,rgba(240,214,170,.8),rgba(240,214,170,0) 100%),
    linear-gradient(90deg,#cdb893 0%,#dcd5bb 35%,#e8ead9 52%,var(--cream) 70%,#f2f3ea 100%)}
.hero-copy{position:absolute;left:605px;top:78px;width:520px}
.hero-brand{display:flex;align-items:center;gap:14px;font-size:46px;color:var(--gold);white-space:nowrap}
.hero-brand .brand-ring{width:72px;height:72px;border-width:3px}
.hero-copy p{margin-top:20px;width:420px;font-family:"Lora",serif;font-style:italic;font-size:13px;line-height:21px;color:#444}
.ticks{margin-top:22px;display:grid;grid-template-columns:222px 220px;row-gap:16px;font-family:"Lora",serif;font-style:italic;font-size:13px;color:#333}
.ticks span{display:flex;align-items:center;gap:10px}
.btn-gold{position:absolute;left:605px;top:362px;width:145px;height:41px;background:linear-gradient(#d6b46b,var(--gold-dark));color:#fff;font-size:14px;font-weight:700;display:flex;align-items:center;justify-content:center;border-radius:2px}
.hero-dots{position:absolute;right:86px;top:452px;display:flex;gap:6px}
.hero-dots i{width:14px;height:14px;border:2px solid var(--ink);border-radius:50%}
.hero-dots i.on{border-color:var(--gold)}

/* section titles */
.sec-title{position:absolute;left:0;width:1200px;display:flex;justify-content:center;align-items:center;gap:10px;font-family:"Playfair Display",serif;font-weight:400;font-size:28px;color:var(--ink)}
.sec-title span{padding:6px 10px;border-top:1px solid #999;border-bottom:1px solid #999}
.emblem{display:block;width:72px;height:72px;border:2px solid var(--gold-light);border-radius:50%;background:radial-gradient(circle,#fff 55%,#f7efdd)}
.sec-title.light{color:#fff}
.sec-title.light span{border-color:#ccc}
.sec-title.light .emblem{background:radial-gradient(circle,#4a433d 55%,#3a3532)}

/* products */
.products{top:636px;height:575px;background:var(--mist)}
.products .sec-title{top:31px}
.prod{position:absolute;top:153px;width:242px;height:346px;background:var(--paper);border:1px solid var(--line);text-align:center}
.prod-img{margin:10px auto 0;width:226px;height:190px;background:linear-gradient(160deg,#f5f5f5,#d9dcdd 60%,#eceeee)}
.price{margin-top:20px;font-size:21px;font-weight:700;color:var(--gold)}
.pname{margin-top:8px;font-size:18px;font-weight:700;color:#222}
.acts{margin-top:14px;display:flex;justify-content:center;gap:8px}
.acts i{width:32px;height:32px;border:1px solid #bbb;border-radius:50%;display:flex;align-items:center;justify-content:center}
.pager{position:absolute;top:544px;left:0;width:1200px;display:flex;justify-content:center;gap:10px}
.pager i{width:9px;height:9px;border-radius:50%;background:var(--ink)}
.pager i.on{background:var(--gold)}

/* blog */
.blog{top:1211px;height:661px;background:var(--paper)}
.blog .sec-title{top:32px}
.post{position:absolute;width:488px;height:212px;border:1px solid var(--line);background:var(--paper)}
.post-img{position:absolute;left:12px;top:12px;width:162px;height:188px}
.post-body{position:absolute;left:200px;top:16px;width:270px}
.post h3{font-size:12px;letter-spacing:.5px;color:#333}
.meta{margin-top:14px;display:flex;gap:18px;font-size:10px;color:var(--gold-dark)}
.post p{margin-top:12px;font-size:11px;line-height:23px;color:#666}
.more{margin-top:4px;font-size:11px;color:var(--gold-dark);text-decoration:underline}

/* consultation */
.consult{top:1872px;height:409px;background:linear-gradient(90deg,#34302d,var(--ink-soft) 55%,#2b2724);overflow:hidden}
.consult-photo{position:absolute;right:0;top:0;width:620px;height:409px;background:radial-gradient(ellipse 55% 80% at 62% 50%,#7a5540,#4e3a2e 50%,rgba(58,53,50,0) 100%)}
.consult .sec-title{width:760px;top:80px}
.consult p{position:absolute;left:130px;top:183px;width:500px;text-align:center;font-family:"Lora",serif;font-style:italic;font-size:13px;line-height:26px;color:#cfcac4}
.btn-line{position:absolute;left:250px;top:285px;width:250px;height:49px;border:1px solid #ddd;color:#fff;font-size:12px;letter-spacing:.5px;display:flex;align-items:center;justify-content:center}

/* brands */
.brands{top:2281px;height:115px;background:linear-gradient(#d5b46e,var(--gold) 55%,#bb974d);display:flex;justify-content:center;align-items:center;gap:10px}
.brands div{width:172px;height:78px;border:1px solid rgba(255,255,255,.35);display:flex;align-items:center;justify-content:center;gap:8px;font-size:21px;font-weight:700;color:#fff}
.brands div i{width:16px;height:16px;border:2px solid #fff;border-radius:50%}

/* latest */
.latest{top:2396px;height:523px;background:var(--paper)}
.latest .sec-title{top:33px}
.article{position:absolute;top:134px;width:330px}
.article-img{width:330px;height:199px}
.article h3{margin-top:32px;font-size:15px;font-weight:700;color:#222}
.article p{margin-top:16px;font-size:11px;line-height:22px;color:#666}
.article .meta{margin-top:14px;font-size:12px}

/* footer */
.site-foot{top:2919px;height:248px;background:var(--foot)}
.col{position:absolute;top:58px}
.col h4{font-size:13px;font-weight:700;letter-spacing:.5px;color:#333;margin-bottom:18px}
.col li{list-style:none;font-size:11px;color:#777;line-height:26px}
.col li::before{content:"›";margin-right:10px;color:#999}
.cards{display:flex;gap:3px}
.cards b{width:40px;height:24px;border:1px solid #bbb;background:#fff;font-size:8px;font-weight:400;color:#555;display:flex;align-items:center;justify-content:center}
.social{margin-top:32px;display:flex;gap:8px}
.social i{width:32px;height:32px;border:1px solid #aaa;border-radius:50%}
.contact li::before{content:none}
.contact li{display:flex;gap:12px;align-items:flex-start}
.contact svg{flex:none;margin-top:8px}
.bottombar{position:absolute;left:0;width:1200px;top:3167px;height:76px;background:var(--ink);display:flex;align-items:center;justify-content:center;font-size:12px;color:#ccc}
</style>
</head>
<body>

<header class="topbar">
  <div class="brand"><i class="brand-ring"></i>Velour Skinhaus</div>
  <div class="util"><span>Doctor</span><span>Pharmacy</span><span>Register</span><span>log in</span></div>
  <div class="lang"><b>EN</b><b class="on">BG</b></div>
  <div class="bag">
    <svg width="20" height="18" viewBox="0 0 20 18"><path d="M1 2h3l2 10h10l2-7H6" fill="none" stroke="#c9a55a" stroke-width="1.8"/><circle cx="8" cy="15.5" r="1.5" fill="#c9a55a"/><circle cx="15" cy="15.5" r="1.5" fill="#c9a55a"/></svg>
  </div>
</header>

<nav class="mainnav">
  <span>Home</span><span>Face</span><span>Body</span><span>Hair Care</span><span>Skin Concerns</span><span>Dermatologist Consultation</span><span>Library</span><span>Contact Us</span>
</nav>

<section class="hero">
  <div class="hero-photo" role="img" aria-label="Full-width luxury hero photograph: woman with long golden curls against a soft cream backdrop"></div>
  <div class="hero-copy">
    <div class="hero-brand"><i class="brand-ring"></i>Velour Skinhaus</div>
    <p>Sed ut perspiciatis unde omnis iste natus error sit voluptatem accusa ntium, totam rem aperiam quasi architecto beatae vitae dicta sunt explicabo.</p>
    <div class="ticks">
      <span><svg width="12" height="10"><path d="M1 5l3 3 7-7" fill="none" stroke="#c9a55a" stroke-width="2"/></svg>Doctor Formulated</span>
      <span><svg width="12" height="10"><path d="M1 5l3 3 7-7" fill="none" stroke="#c9a55a" stroke-width="2"/></svg>Registered Pharmacy</span>
      <span><svg width="12" height="10"><path d="M1 5l3 3 7-7" fill="none" stroke="#c9a55a" stroke-width="2"/></svg>Freshly Handmade</span>
      <span><svg width="12" height="10"><path d="M1 5l3 3 7-7" fill="none" stroke="#c9a55a" stroke-width="2"/></svg>Highest Ethical Standards</span>
    </div>
  </div>
  <div class="btn-gold">Learn More</div>
  <div class="hero-dots"><i></i><i></i><i class="on"></i><i></i><i></i></div>
</section>

<section class="products">
  <h2 class="sec-title"><span>Featured</span><i class="emblem"></i><span>Products</span></h2>
  <div class="prod" style="left:86px"><div class="prod-img" role="img" aria-label="Silver cosmetic jars and bottles"></div><div class="price">$25.00</div><div class="pname">Contrary Popular</div><div class="acts"><i><svg width="14" height="12"><path d="M1 1h2l2 7h7l1-5H4" fill="none" stroke="#999"/></svg></i><i><svg width="14" height="12"><path d="M7 11L2 6a3 3 0 0 1 5-4 3 3 0 0 1 5 4z" fill="none" stroke="#999"/></svg></i><i><svg width="14" height="12"><path d="M2 4h10M2 8h10" stroke="#999"/></svg></i></div></div>
  <div class="prod" style="left:348px"><div class="prod-img" role="img" aria-label="Pink cream tube beside its box"></div><div class="price">$25.00</div><div class="pname">Contrary Popular</div><div class="acts"><i><svg width="14" height="12"><path d="M1 1h2l2 7h7l1-5H4" fill="none" stroke="#999"/></svg></i><i><svg width="14" height="12"><path d="M7 11L2 6a3 3 0 0 1 5-4 3 3 0 0 1 5 4z" fill="none" stroke="#999"/></svg></i><i><svg width="14" height="12"><path d="M2 4h10M2 8h10" stroke="#999"/></svg></i></div></div>
  <div class="prod" style="left:612px"><div class="prod-img" role="img" aria-label="Set of teal and white serum bottles"></div><div class="price">$25.00</div><div class="pname">Contrary Popular</div><div class="acts"><i><svg width="14" height="12"><path d="M1 1h2l2 7h7l1-5H4" fill="none" stroke="#999"/></svg></i><i><svg width="14" height="12"><path d="M7 11L2 6a3 3 0 0 1 5-4 3 3 0 0 1 5 4z" fill="none" stroke="#999"/></svg></i><i><svg width="14" height="12"><path d="M2 4h10M2 8h10" stroke="#999"/></svg></i></div></div>
  <div class="prod" style="left:871px"><div class="prod-img" role="img" aria-label="White cream tube"></div><div class="price">$25.00</div><div class="pname">Contrary Popular</div><div class="acts"><i><svg width="14" height="12"><path d="M1 1h2l2 7h7l1-5H4" fill="none" stroke="#999"/></svg></i><i><svg width="14" height="12"><path d="M7 11L2 6a3 3 0 0 1 5-4 3 3 0 0 1 5 4z" fill="none" stroke="#999"/></svg></i><i><svg width="14" height="12"><path d="M2 4h10M2 8h10" stroke="#999"/></svg></i></div></div>
  <div class="pager"><i></i><i class="on"></i><i></i></div>
</section>

<section class="blog">
  <h2 class="sec-title"><span>Blog</span><i class="emblem"></i><span>Articles</span></h2>
  <article class="post" style="left:86px;top:134px"><div class="post-img" role="img" aria-label="Woman with water splash, skincare scene" style="background:linear-gradient(135deg,#dfe8ea,#b8c9cf)"></div><div class="post-body"><h3>SED UT PERSPICIATIS UNDE OMNIS....</h3><div class="meta"><span>▦ 25 Aug 2020</span><span>○ Comments 20</span><span>♡ 14 Likes</span></div><p>Sed ut perspiciatis unde omnis iste natus error sit voluptatem accusantium doloremque laudantium, totam rem aperiam, eaque ipsa quae ab illo inven beatae vitae dicta sunt explicabo.</p><div class="more">Read More</div></div></article>
  <article class="post" style="left:625px;top:134px"><div class="post-img" role="img" aria-label="Long glossy brown hair" style="background:linear-gradient(135deg,#8a5a3a,#c49a74)"></div><div class="post-body"><h3>SED UT PERSPICIATIS UNDE OMNIS....</h3><div class="meta"><span>▦ 25 Aug 2020</span><span>○ Comments 20</span><span>♡ 14 Likes</span></div><p>Sed ut perspiciatis unde omnis iste natus error sit voluptatem accusantium doloremque laudantium, totam rem aperiam, eaque ipsa quae ab illo inven beatae vitae dicta sunt explicabo.</p><div class="more">Read More</div></div></article>
  <article class="post" style="left:86px;top:393px"><div class="post-img" role="img" aria-label="Body care massage scene" style="background:linear-gradient(135deg,#f1ece6,#d8c2ad)"></div><div class="post-body"><h3>SED UT PERSPICIATIS UNDE OMNIS....</h3><div class="meta"><span>▦ 25 Aug 2020</span><span>○ Comments 20</span><span>♡ 14 Likes</span></div><p>Sed ut perspiciatis unde omnis iste natus error sit voluptatem accusantium doloremque laudantium, totam rem aperiam, eaque ipsa quae ab illo inven beatae vitae dicta sunt explicabo.</p><div class="more">Read More</div></div></article>
  <article class="post" style="left:625px;top:393px"><div class="post-img" role="img" aria-label="Portrait with clear glowing skin" style="background:linear-gradient(135deg,#f6e6da,#dcb79e)"></div><div class="post-body"><h3>SED UT PERSPICIATIS UNDE OMNIS....</h3><div class="meta"><span>▦ 25 Aug 2020</span><span>○ Comments 20</span><span>♡ 14 Likes</span></div><p>Sed ut perspiciatis unde omnis iste natus error sit voluptatem accusantium doloremque laudantium, totam rem aperiam, eaque ipsa quae ab illo inven beatae vitae dicta sunt explicabo.</p><div class="more">Read More</div></div></article>
</section>

<section class="consult">
  <div class="consult-photo" role="img" aria-label="Woman with dark voluminous curls, consultation banner image"></div>
  <h2 class="sec-title light"><span>Dermatologist</span><i class="emblem"></i><span>Consultation</span></h2>
  <p>Sed ut perspiciatis unde omnis iste natus error sit voluptatem accusantium doloremque laudantium, totam rem aperiam, eaque ipsa quae ab illo inventore veritatis et quasi architecto beatae vitae dicta sunt explicabo.</p>
  <div class="btn-line">CLICK HERE FOR MORE INFO</div>
</section>

<section class="brands">
  <div><i></i>Lumora</div><div><i></i>Ostrel</div><div><i></i>Veyla</div><div><i></i>Quadrin</div><div><i></i>Paneth</div><div>Stillwax</div>
</section>

<section class="latest">
  <h2 class="sec-title"><span>Latest</span><i class="emblem"></i><span>Articles</span></h2>
  <article class="article" style="left:86px"><div class="article-img" role="img" aria-label="Smiling woman touching her face" style="background:linear-gradient(120deg,#f3e3d8,#e6e6e6)"></div><h3>NEQUE PORRO QUISQUAM</h3><p>Sed ut perspiciatis unde omnis iste natus error sit voluptatem accusantiumue ipsa beatae vitae dicta sunt explicabo.</p><div class="meta"><span>▦ 1 month ago</span><span>○ 05 Comments</span></div></article>
  <article class="article" style="left:437px"><div class="article-img" role="img" aria-label="Woman with flowing brown curls" style="background:linear-gradient(120deg,#e9e4df,#7a5540 55%,#d9d2cb)"></div><h3>NEQUE PORRO QUISQUAM</h3><p>Sed ut perspiciatis unde omnis iste natus error sit voluptatem accusantiumue ipsa beatae vitae dicta sunt explicabo.</p><div class="meta"><span>▦ 1 month ago</span><span>○ 05 Comments</span></div></article>
  <article class="article" style="left:785px"><div class="article-img" role="img" aria-label="Sunbathers on loungers by the sea" style="background:linear-gradient(120deg,#f4efe9,#c79a76 50%,#efe8e0)"></div><h3>NEQUE PORRO QUISQUAM</h3><p>Sed ut perspiciatis unde omnis iste natus error sit voluptatem accusantiumue ipsa beatae vitae dicta sunt explicabo.</p><div class="meta"><span>▦ 1 month ago</span><span>○ 05 Comments</span></div></article>
</section>

<footer class="site-foot">
  <div class="col" style="left:93px"><h4>PAYMENTS ACCEPTED</h4><div class="cards"><b>Cardo</b><b>Duopay</b><b>Amvera</b><b>Nexpay</b></div><div class="social"><i></i><i></i><i></i><i></i><i></i></div></div>
  <div class="col" style="left:346px"><h4>POPULAR BRANDS</h4><ul><li>Doctor Formulated</li><li>Freshly Handmade</li><li>Registered Pharmacy</li><li>Highest Ethical Standards</li></ul></div>
  <div class="col" style="left:573px"><h4>CATEGORIES</h4><ul><li>Face</li><li>Body</li><li>Hair Care</li><li>Skin Concerns</li><li>Dermatologist</li></ul></div>
  <div class="col" style="left:755px"><h4>MY ACCOUNT</h4><ul><li>My account</li><li>Orders</li><li>Addresses</li><li>Shopping cart</li><li>Wishlist</li></ul></div>
  <div class="col contact" style="left:938px"><h4>CONTACT US</h4><ul>
    <li><svg width="12" height="12"><rect x="1" y="1" width="10" height="10" rx="2" fill="#999"/></svg>(000)-555-0142 (Phone)</li>
    <li><svg width="12" height="12"><rect x="1" y="3" width="10" height="7" fill="#999"/></svg>(000)-555-0142 (Fax)</li>
    <li><svg width="12" height="12"><rect x="1" y="2" width="10" height="8" fill="none" stroke="#999"/><path d="M1 2l5 4 5-4" fill="none" stroke="#999"/></svg>info@velourskinhaus.com</li>
    <li><svg width="12" height="14"><path d="M6 13C2 8 1 6 1 5a5 5 0 0 1 10 0c0 1-1 3-5 8z" fill="#999"/></svg><span style="line-height:16px;padding-top:4px"># 52 Lorem ipsum dummy<br>Lorem Ipsum Dummy</span></li>
  </ul></div>
</footer>

<div class="bottombar">© Copyright 2016 Velour Skinhaus. All Rights Reserved</div>

</body>
</html>
```